Modern Business Card

Modern professional business card with more than just logo and demographic info. Something memorable.

We are a trendy/modern chiropractic group with an emphasis on neurology, hence the minimalist-type brain logo. We want to convey that modern and technical aspect with professionalism and the elite nature of our practice environment.

```html
<!DOCTYPE html>
<html lang="en">
<head>
<meta charset="utf-8">
<title>Meridian Chiropractic – Business Card</title>
<link href="https://fonts.googleapis.com/css2?family=Cinzel:wght@400;500&family=Montserrat:wght@400;500&display=swap" rel="stylesheet">
<style>
  :root {
    --backdrop: #2f2927;
    --card-white: #ffffff;
    --card-black: #1b1b1b;
    --brand-blue: #4a82c6;
    --ink-dark: #1e1e1e;
    --ink-grey: #5a5a5a;
    --ink-light: #f2f2f2;
  }
  * { margin: 0; padding: 0; box-sizing: border-box; }
  html, body { width: 1200px; height: 716px; overflow: hidden; background: var(--backdrop); }
  .canvas { position: relative; width: 1200px; height: 716px; }

  .card {
    position: absolute;
    top: 210px;
    width: 520px;
    height: 297px;
    overflow: hidden;
    border-radius: 3px;
    box-shadow: 0 14px 30px rgba(0,0,0,.45);
  }
  .card--front { left: 50px; background: var(--card-white); }
  .card--back { left: 630px; background: var(--card-black); }

  .front-band {
    position: absolute; left: 0; right: 0; bottom: 0; height: 122px;
    background: var(--card-black);
  }

  .accent-pill {
    position: absolute;
    background: var(--brand-blue);
    border-radius: 36px;
  }
  .card--front .accent-pill {
    left: 392px; top: 118px; width: 72px; height: 210px;
    box-shadow: 0 0 0 7px var(--card-white);
  }
  .card--back .accent-pill {
    left: 52px; top: 34px; width: 72px; height: 230px;
  }

  .wordmark { position: absolute; font-family: "Cinzel", serif; line-height: .9; }
  .wordmark__main { display: block; font-weight: 500; }
  .wordmark__sub { display: block; font-weight: 400; letter-spacing: .02em; }

  .card--front .wordmark { left: 40px; top: 34px; color: var(--ink-dark); }
  .card--front .wordmark__main { font-size: 30px; }
  .card--front .wordmark__sub { font-size: 17px; }

  .person { position: absolute; left: 40px; top: 110px; }
  .person__name {
    font-family: "Cinzel", serif; font-size: 17px; font-weight: 500;
    color: var(--brand-blue); letter-spacing: .02em;
  }
  .person__role {
    font-family: "Montserrat", sans-serif; font-size: 11px;
    color: var(--ink-grey); margin-top: 3px;
  }

  .contact-list {
    position: absolute; left: 40px; top: 196px; list-style: none;
    font-family: "Montserrat", sans-serif; font-size: 11.5px; color: var(--ink-light);
  }
  .contact-list li { display: flex; align-items: center; gap: 8px; margin-bottom: 6px; }
  .contact-list svg { width: 10px; height: 10px; fill: none; stroke: var(--ink-light); stroke-width: 1.4; }

  .address {
    position: absolute; left: 222px; top: 236px;
    font-family: "Montserrat", sans-serif; font-size: 11.5px; line-height: 1.55; color: var(--ink-light);
    font-style: normal;
  }

  .brand-lockup {
    position: absolute; left: 190px; top: 112px;
    display: flex; align-items: center; gap: 16px;
  }
  .brand-lockup__square { width: 38px; height: 38px; background: var(--brand-blue); border-radius: 4px; }
  .card--back .wordmark { position: static; color: var(--ink-light); }
  .card--back .wordmark__main { font-size: 38px; }
  .card--back .wordmark__sub { font-size: 22px; }
</style>
</head>
<body>
<main class="canvas">

  <section class="card card--front" aria-label="Business card front">
    <div class="wordmark">
      <span class="wordmark__main">Meridian</span>
      <span class="wordmark__sub">Chiropractic</span>
    </div>
    <div class="person">
      <p class="person__name">Daniel Whitmore</p>
      <p class="person__role">Director</p>
    </div>
    <div class="front-band"></div>
    <div class="accent-pill"></div>
    <ul class="contact-list">
      <li>
        <svg viewBox="0 0 10 10"><path d="M2 1h2l1 2.5-1.3 1a5 5 0 0 0 2.3 2.3l1-1.3L9.5 6.5v2a1 1 0 0 1-1 1A8 8 0 0 1 1 2a1 1 0 0 1 1-1z"/></svg>
        (555) 210-4837
      </li>
      <li>
        <svg viewBox="0 0 10 10"><rect x="1" y="2" width="8" height="6"/><path d="M1 2l4 3.5L9 2"/></svg>
        info@meridianchiro.com
      </li>
      <li>
        <svg viewBox="0 0 10 10"><circle cx="5" cy="5" r="4"/><path d="M1 5h8M5 1c-2 2.5-2 5.5 0 8M5 1c2 2.5 2 5.5 0 8"/></svg>
        www.meridianchiro.com
      </li>
    </ul>
    <address class="address">1187 Larkspur Lane<br>Salem, OR 97301</address>
  </section>

  <section class="card card--back" aria-label="Business card back">
    <div class="accent-pill"></div>
    <div class="brand-lockup">
      <span class="brand-lockup__square"></span>
      <div class="wordmark">
        <span class="wordmark__main">Meridian</span>
        <span class="wordmark__sub">Chiropractic</span>
      </div>
    </div>
  </section>

</main>
</body>
</html>
```